Ledgerwise Forge - WordPress Theme & Logo

Design a logo and Wordpress website design for Ledgerwise Forge. Ledgerwise Forge provides cryptocurrency development services to clients who need a team to create & continue developing a new cryptocurrency or who want to replace their current cryptocurrency development team. more details in the attached document.
Updates

Target Market(s)

Entrepreneurs who are building a business / platform that makes use of an underlying cryptocurrency.

Logo Text

LF or Ledgerwise Forge

Coding

Coded - Design and coding required

Font styles to use
Sans Serif

Requirements
Must have
• Professional logo, complete coded Wordpress theme for all pages, containing all specified links and buttons
Nice to have
• It would be nice if the buttons that are meant to integrate with Dealtrail contain the necessary code for that. I can provide any necessary Dealtrail details from my account.
Should not have
• Slow loading time

```html
<!DOCTYPE html>
<html lang="en">
<head>
<meta charset="utf-8">
<title>Ledgerwise Forge</title>
<link href="https://fonts.googleapis.com/css2?family=Montserrat:wght@400;600;700&family=Roboto:ital,wght@0,400;0,500;0,700;1,400&display=swap" rel="stylesheet">
<style>
:root{
  --blue:#0b68b5;
  --blue-dark:#0a4f8c;
  --ink:#1b1b1b;
  --text:#555;
  --muted:#777;
  --footer:#363636;
  --white:#fff;
  --hero-a:#0c3a45;
  --hero-b:#145a66;
}
*{margin:0;padding:0;box-sizing:border-box}
html,body{width:1200px;height:3784px;overflow:hidden}
body{position:relative;font-family:Roboto,Arial,sans-serif;color:var(--text);background:var(--white)}
.abs{position:absolute}
h1,h2,h3,.logo{font-family:Montserrat,Arial,sans-serif;color:var(--ink)}
.btn{position:absolute;display:flex;align-items:center;justify-content:center;background:var(--blue);color:var(--white);font:700 13px Roboto,sans-serif;text-transform:uppercase;border-radius:3px;white-space:nowrap}

/* hero */
.hero{left:0;top:0;width:1200px;height:600px;background:radial-gradient(ellipse at 75% 40%,var(--hero-b),var(--hero-a) 60%,#071f27)}
.hero-art{left:540px;top:60px;width:480px;height:520px;background:radial-gradient(circle at 50% 50%,rgba(60,90,100,.7),rgba(20,50,60,0) 70%)}
.logo{font-size:17px;font-weight:700;color:var(--white);letter-spacing:.3px;white-space:nowrap}
.logo span{font-weight:400}
.nav{top:34px;left:439px;display:flex;gap:29px;font:700 13px Roboto,sans-serif;color:var(--white);white-space:nowrap}
.hero h1{left:92px;top:196px;width:620px;font-size:27px;line-height:36px;color:var(--white);font-weight:700}
.hero p{left:92px;top:320px;width:560px;font-size:13px;line-height:26px;color:#e8f0f2;white-space:nowrap}

/* why */
.section-title{left:0;width:1200px;text-align:center;font-size:27px;line-height:34px;font-weight:700}
.why-card{width:316px;height:309px}
.why-card .photo{left:0;top:0;width:316px;height:206px;border:4px solid #fff;box-shadow:0 0 6px rgba(0,0,0,.25)}
.why-card .box{left:25px;top:174px;width:270px;height:135px;background:var(--white);border-bottom:4px solid var(--blue);text-align:center;box-shadow:0 2px 8px rgba(0,0,0,.08)}
.why-card h3{margin-top:32px;font:500 16px Roboto,sans-serif;color:var(--ink)}
.why-card p{margin:12px auto 0;width:250px;font-size:13.5px;line-height:20px;color:var(--muted);white-space:nowrap}

/* who */
.who{left:0;top:1224px;width:1200px;height:483px;background:linear-gradient(90deg,#0a1a3a,#0d3f7a 45%,#0a2550 80%,#050d22)}
.who-box{left:106px;top:1297px;width:501px;height:337px;background:var(--white);border-top:5px solid var(--blue);border-bottom:5px solid var(--blue)}
.who-box h2{position:absolute;left:35px;top:40px;font-size:25px}
.who-box p{position:absolute;left:35px;top:92px;width:440px;font-size:13px;line-height:26px;color:var(--text);white-space:nowrap}
.who-box a{color:var(--blue);text-decoration:underline}

/* testimonials */
.t-card{width:317px;height:219px;background:var(--white);box-shadow:0 0 8px rgba(0,0,0,.15);text-align:center}
.t-card .avatar{position:absolute;left:123px;top:-32px;width:70px;height:70px;border-radius:50%;border:4px solid #fff;box-shadow:0 0 6px rgba(0,0,0,.25);background:linear-gradient(#9fb2c2,#3a4b5e)}
.t-card .quote{position:absolute;left:0;width:100%;top:60px;font:700 48px Georgia,serif;color:var(--blue);line-height:40px;height:26px;overflow:hidden}
.t-card p{position:absolute;left:0;top:96px;width:100%;font-style:italic;font-size:13.5px;line-height:24px;color:var(--muted);white-space:nowrap}
.t-card .who-name{position:absolute;left:0;width:100%;top:182px;font-size:13.5px;color:var(--muted)}
.t-card .who-name b{color:var(--blue)}

/* services */
.svc-intro{left:150px;top:2305px;width:900px;text-align:center;font-size:13px;line-height:26px;color:var(--muted);white-space:nowrap}
.svc{width:478px;height:247px;background:var(--white);box-shadow:0 0 8px rgba(0,0,0,.15)}
.svc .photo{left:4px;top:4px;width:225px;height:239px}
.svc h3{position:absolute;left:255px;top:26px;width:200px;font:700 13.5px Roboto,sans-serif;line-height:19px;color:var(--ink);text-transform:uppercase}
.svc ul{position:absolute;left:255px;list-style:none;font-size:12.5px;line-height:22.5px;color:var(--muted);white-space:nowrap}
.svc li::before{content:"»";color:var(--blue);margin-right:14px}
.svc .more{position:absolute;left:255px;top:204px;font:700 12.5px Roboto,sans-serif;color:var(--blue);display:flex;align-items:center;gap:8px}

/* schedule */
.schedule{left:0;top:3104px;width:1200px;height:292px;background:linear-gradient(90deg,#0b5eac,#0d6ec4 50%,#0b5eac)}
.schedule h2{position:absolute;left:0;top:42px;width:100%;text-align:center;color:var(--white);font-size:27px}
.schedule p{position:absolute;left:150px;top:98px;width:900px;text-align:center;color:var(--white);font-size:13px;line-height:26px;white-space:nowrap}
.btn-outline{left:483px;top:180px;width:234px;height:46px;background:var(--blue);border:2px solid var(--white)}

/* footer */
.footer{left:0;top:3396px;width:1200px;height:388px;background:var(--footer);color:#e6e6e6}
.footer .logo{position:absolute;left:110px;top:75px;font-size:19px}
.footer .about{position:absolute;left:110px;top:116px;width:290px;font-size:13.5px;line-height:26px;white-space:nowrap}
.footer h4{position:absolute;font:700 14px Roboto,sans-serif;color:var(--white);top:74px}
.footer ul{position:absolute;top:108px;list-style:none;font-size:13.5px;line-height:30px;white-space:nowrap}
.footer li::before{content:"»";margin-right:20px}
.news-input{left:797px;top:3503px;width:187px;height:39px;background:var(--white);font-size:13px;color:#888;padding:11px 14px}
.news-btn{left:984px;top:3503px;width:101px;height:39px;background:var(--blue);color:var(--white);font:700 12.5px Roboto,sans-serif;display:flex;align-items:center;justify-content:center}
.social{top:3565px;width:34px;height:34px;border:2px solid var(--white);border-radius:50%}
.rule{left:110px;top:3702px;width:980px;height:1px;background:#777}
.copy{left:0;top:3728px;width:1200px;text-align:center;font-size:13.5px;color:var(--white)}
</style>
</head>
<body>

<!-- Hero -->
<section class="abs hero">
  <div class="abs hero-art" role="img" aria-label="Glowing 3D cube over a network of connected nodes"></div>
  <div class="abs logo" style="left:110px;top:34px">LEDGERWISE <span>FORGE</span></div>
  <nav class="abs nav"><span>SERVICES</span><span>LEDGERWISE FORGE METHOD</span><span>TESTIMONIALS</span><span>BLOG</span><span>ABOUT US</span></nav>
  <h1 class="abs">YOUR CRYPTOCURRENCY SECURE ,<br>EAST TO USE &amp; BUILT BT AN EXPERT<br>TEAM</h1>
  <p class="abs">Ledgerwise Forge adds professionalism to cryptocurrency development. Our<br>done-for-you service covers everything from development and IT operations to<br>ongoing support. You have access to a full team, for less than the typical</p>
  <div class="btn" style="left:92px;top:414px;width:235px;height:47px">Schedule Free Consultation</div>
</section>

<!-- Why choose -->
<h2 class="abs section-title" style="top:690px">WHY CHOOSE LEDGERWISE<br>FORGE</h2>

<div class="abs why-card" style="left:110px;top:803px">
  <div class="abs photo" role="img" aria-label="Hand holding a gold coin above a laptop" style="background:linear-gradient(135deg,#6b5a4a,#2c2a2c)"></div>
  <div class="abs box"><h3>VALUE</h3><p>A team of experts, regular updates,<br>and fixed costs</p></div>
</div>
<div class="abs why-card" style="left:441px;top:803px">
  <div class="abs photo" role="img" aria-label="Laptop showing a trading chart between reaching hands" style="background:linear-gradient(135deg,#9aa1a3,#3b4144)"></div>
  <div class="abs box"><h3>SUPPORT</h3><p>Receive advice and other services,<br>beyond development.</p></div>
</div>
<div class="abs why-card" style="left:771px;top:803px">
  <div class="abs photo" role="img" aria-label="Business team reviewing financial charts" style="background:linear-gradient(135deg,#3d5a7a,#1a2233)"></div>
  <div class="abs box"><h3>COMMITMENT</h3><p>Enjoy regular updates and<br>new features.</p></div>
</div>

<!-- Who we are -->
<section class="abs who" role="img" aria-label="Businessman touching a glowing hexagon network of coin symbols"></section>
<div class="abs who-box">
  <h2>WHO WE ARE</h2>
  <p>In addition to creating and enhancing cryptocurrencies for clients, the<br>Ledgerwise Forge team has been running the <a>Qorva cryptocurrency</a><br>since 2017. We prefer long-term relationships, enabling us to deliver<br>the very highest quality and giving you peace of mind that you've got a<br>professional and trustworthy team at your side.</p>
  <div class="btn" style="left:35px;top:240px;width:235px;height:47px">Schedule Free Consultation</div>
</div>

<!-- Testimonials -->
<h2 class="abs section-title" style="top:1803px">CLIENT TESTIMONIALS</h2>
<div class="abs t-card" style="left:109px;top:1921px">
  <div class="avatar" role="img" aria-label="Client portrait"></div><div class="quote">“</div>
  <p>Lorem ipsum dolor sit amet, consec<br>tetur adipiscing elit, sed do eiusmtempor<br>incididunt ut labore et dolore magna</p>
  <div class="who-name"><b>ARLO VANCE</b> , Businessman</div>
</div>
<div class="abs t-card" style="left:441px;top:1921px">
  <div class="avatar" role="img" aria-label="Client portrait"></div><div class="quote">“</div>
  <p>Lorem ipsum dolor sit amet, consec<br>tetur adipiscing elit, sed do eiusmtempor<br>incididunt ut labore et dolore magna</p>
  <div class="who-name"><b>ARLO VANCE</b> , Businessman</div>
</div>
<div class="abs t-card" style="left:774px;top:1921px">
  <div class="avatar" role="img" aria-label="Client portrait"></div><div class="quote">“</div>
  <p>Lorem ipsum dolor sit amet, consec<br>tetur adipiscing elit, sed do eiusmtempor<br>incididunt ut labore et dolore magna</p>
  <div class="who-name"><b>ARLO VANCE</b> , Businessman</div>
</div>

<!-- Services -->
<h2 class="abs section-title" style="top:2254px">OUR SERVICES</h2>
<p class="abs svc-intro">Ledgerwise Forge provides a complete service that handles the development, IT operations and support for your<br>cryptocurrency. Cryptocurrency development can be difficult and complex, and a quality development team is hard to find and<br>expensive. Ledgerwise Forge has an experienced team that has helped several clients launch and enhance<br>their cryptocurrencies, including successfully running the Qorva cryptocurrency since 2017, and writing a next-generation<br>cryptocurrency from scratch.</p>

<div class="abs svc" style="left:112px;top:2483px">
  <div class="abs photo" role="img" aria-label="Hands over financial reports with glowing chart" style="background:linear-gradient(135deg,#c9a27a,#2f5f8c)"></div>
  <h3>Blockchain Creation &amp; Launch</h3>
  <ul style="top:68px"><li>Lower cost per month</li><li>Slower release schedule</li><li>Client assists with testing</li><li>Less input into future roadmap</li><li>Limited support hours/priority</li></ul>
  <div class="more">LEARN MORE <svg width="12" height="12" viewBox="0 0 12 12"><circle cx="6" cy="6" r="6" fill="#0b68b5"/><path d="M4 3.5 6.8 6 4 8.5M6.5 6H3" stroke="#fff" stroke-width="1.6" fill="none"/></svg></div>
</div>
<div class="abs svc" style="left:608px;top:2483px">
  <div class="abs photo" role="img" aria-label="Skyscrapers linked by a network of lines" style="background:linear-gradient(135deg,#5d8ac0,#1d3550)"></div>
  <h3>Basic Offering</h3>
  <ul style="top:56px"><li>Lower cost per month</li><li>Slower release schedule</li><li>Client assists with testing</li><li>Less input into future roadmap</li><li>Limited support hours/priority</li></ul>
  <div class="more">LEARN MORE <svg width="12" height="12" viewBox="0 0 12 12"><circle cx="6" cy="6" r="6" fill="#0b68b5"/><path d="M4 3.5 6.8 6 4 8.5M6.5 6H3" stroke="#fff" stroke-width="1.6" fill="none"/></svg></div>
</div>
<div class="abs svc" style="left:112px;top:2757px">
  <div class="abs photo" role="img" aria-label="Person working at a laptop with trading screens" style="background:linear-gradient(135deg,#e4e7ea,#6f7680)"></div>
  <h3>Full Service Offering</h3>
  <ul style="top:46px"><li>Mid-range cost per month</li><li>Releases every 1.5 - 2 months</li><li>Client can help request/</li><li>Full testing by my team prior</li><li>Priority support</li></ul>
  <div class="more">LEARN MORE <svg width="12" height="12" viewBox="0 0 12 12"><circle cx="6" cy="6" r="6" fill="#0b68b5"/><path d="M4 3.5 6.8 6 4 8.5M6.5 6H3" stroke="#fff" stroke-width="1.6" fill="none"/></svg></div>
</div>
<div class="abs svc" style="left:608px;top:2757px">
  <div class="abs photo" role="img" aria-label="Hands presenting colourful glowing data blocks" style="background:linear-gradient(135deg,#1a3050,#2b7ad0 50%,#c02a8a)"></div>
  <h3>Blockchain Creation &amp; Launch</h3>
  <ul style="top:62px"><li>Higher cost per month</li><li>Release frequency up to once</li><li>Dedicated development lead</li><li>Ability to request custom features</li><li>Priority 24/7 support</li></ul>
  <div class="more">LEARN MORE <svg width="12" height="12" viewBox="0 0 12 12"><circle cx="6" cy="6" r="6" fill="#0b68b5"/><path d="M4 3.5 6.8 6 4 8.5M6.5 6H3" stroke="#fff" stroke-width="1.6" fill="none"/></svg></div>
</div>

<!-- Schedule -->
<section class="abs schedule">
  <h2>SCHEDULE NOW</h2>
  <p>Lorem ipsum dolor sit amet, consectetur adipiscing elit, sed do eiusmod tempor incididunt ut labore et dolore magna<br>aliqua. Ut enim ad minim veniam, quis nostrud exercitation ullamco laboris nisi ut aliquip</p>
  <div class="btn btn-outline">Schedule Free Consultation</div>
</section>

<!-- Footer -->
<footer class="abs footer">
  <div class="logo">LEDGERWISE <span>FORGE</span></div>
  <p class="about">Lorem ipsum dolor sit ame consectetur<br>adipiscing elit, sed do eiusmod tempor<br>incididunt ut labore et dolore magna<br>aliqua</p>
  <h4 style="left:428px">NAVIGATE</h4>
  <ul style="left:428px"><li>Home</li><li>About Us</li><li>Our Services</li><li>Reviews</li><li>Contact Us</li></ul>
  <ul style="left:587px"><li>Terms &amp; Conditions</li><li>Privacy Policy</li><li>Help Service</li><li>FAQ</li><li>BLog</li></ul>
  <h4 style="left:796px">GET OUR NEWSLETTER</h4>
</footer>
<div class="abs news-input">Email Adress</div>
<div class="abs news-btn">SUBSCRIBE</div>
<div class="abs social" style="left:798px"></div>
<div class="abs social" style="left:838px"></div>
<div class="abs social" style="left:878px"></div>
<div class="abs social" style="left:918px"></div>
<div class="abs rule"></div>
<div class="abs copy">© 2021 Ledgerwise Forge. All Rights Reserved</div>

</body>
</html>
```